Card design for orthopaedic surgeons working as The Brightwater Joint Centre

Business cards, letterhead

Colors

Designer to choose colors to be used in the design.

Requirements
Must have
• Late addition.
• Cards letterhead must have logos of
• Crestmoor Lindell College of Surgeons
• Varenwood Bone Health Association
Nice to have
• Back of card to have space for appointment time to be added by hand and some blank space for writing incidental other notes.

```html
<!DOCTYPE html>
<html lang="en">
<head>
<meta charset="utf-8">
<title>The Brightwater Joint Centre – Stationery</title>
<link href="https://fonts.googleapis.com/css2?family=Roboto:wght@400;500&display=swap" rel="stylesheet">
<style>
  :root {
    --navy: #062f49;
    --sky: #4aa3dc;
    --ink: #1b2a3a;
    --backdrop: #c8c8c8;
    --paper: #ffffff;
    --line: #8a96a3;
  }
  html, body {
    margin: 0; padding: 0;
    width: 1200px; height: 763px;
    overflow: hidden;
    background: var(--backdrop);
    font-family: "Roboto", Arial, sans-serif;
    color: var(--ink);
  }
  .stage { position: relative; width: 1200px; height: 763px; }
  .sheet, .card {
    position: absolute;
    background: var(--paper);
    overflow: hidden;
  }
  .sheet { left: 47px; top: 12px; width: 579px; height: 735px; box-shadow: 0 0 2px rgba(0,0,0,.25); }
  .card { left: 659px; width: 441px; height: 254px; border-radius: 12px; box-shadow: 0 1px 4px rgba(0,0,0,.3); }
  .card--front { top: 114px; }
  .card--appointment { top: 401px; }
  .brand {
    position: absolute;
    display: flex; align-items: center; gap: 5px;
    color: var(--navy);
    font-weight: 500;
    white-space: nowrap;
  }
  .brand__dot { border-radius: 50%; background: var(--sky); flex: none; }
  .sheet .brand { left: 37px; top: 63px; font-size: 15px; }
  .sheet .brand__dot { width: 10px; height: 10px; }
  .card--front .brand { left: 30px; top: 73px; font-size: 13.5px; }
  .card--front .brand__dot { width: 9px; height: 9px; }
  .card--appointment .brand { left: 26px; top: 37px; font-size: 11px; }
  .card--appointment .brand__dot { width: 7px; height: 7px; }
  .badge { position: absolute; border-radius: 6px; }
  .badge--college { background: linear-gradient(160deg, #d9b56a, #b8473a 55%, #3e6a4e); }
  .badge--association { background: linear-gradient(170deg, #c9b27a, #8fa4b8 60%, #b7bec7); }
  .sheet .badge--college { left: 43px; top: 630px; width: 66px; height: 72px; }
  .sheet .badge--association { left: 124px; top: 633px; width: 75px; height: 69px; }
  .card--front .badge--college { left: 31px; top: 108px; width: 78px; height: 87px; }
  .card--front .badge--association { left: 130px; top: 112px; width: 90px; height: 84px; }
  .contact { position: absolute; line-height: 1.5; }
  .contact p { margin: 0; }
  .contact .icon { display: inline-block; vertical-align: -1px; margin-right: 3px; }
  .sheet .contact { left: 417px; top: 35px; font-size: 8.5px; }
  .sheet .contact .gap { margin-top: 6px; }
  .sheet .contact .row { line-height: 1.5; }
  .card--front .divider { position: absolute; left: 237px; top: 66px; width: 1px; height: 123px; background: var(--sky); }
  .card--front .contact { left: 254px; top: 63px; font-size: 10.5px; }
  .person__name { color: var(--sky); font-weight: 500; font-size: 14.5px; line-height: 1.2; }
  .person__title { font-weight: 500; font-size: 11px; margin-bottom: 6px !important; }
  .card--front .gap { margin-top: 7px; }
  .card--front .row { font-size: 11px; line-height: 1.45; }
  .wave { position: absolute; left: 0; display: block; }
  .sheet .wave { top: 672px; width: 579px; height: 63px; }
  .card--front .wave { top: 210px; width: 441px; height: 44px; }
  .appointment { position: absolute; left: 26px; top: 111px; right: 22px; font-size: 11.5px; }
  .appointment__title { margin: 0 0 22px; font-size: 14.5px; font-weight: 500; color: var(--navy); }
  .appointment__title span { color: var(--sky); }
  .field-row { display: flex; align-items: baseline; height: 23.5px; white-space: nowrap; }
  .leader { flex: 1; border-bottom: 1px dotted var(--line); margin: 0 4px 0 3px; transform: translateY(-2px); }
  .leader--short { flex: 0 0 118px; }
  .check { display: inline-block; width: 7px; height: 7px; border: 1.5px solid var(--ink); margin-right: 3px; vertical-align: 0; }
  .option { margin-right: 9px; }
  .days { display: flex; justify-content: space-between; height: 20px; align-items: baseline; }
  .note { margin: 0; font-size: 11.2px; white-space: nowrap; }
</style>
</head>
<body>
<div class="stage">

  <section class="sheet" aria-label="Letterhead">
    <div class="brand"><span class="brand__dot"></span>The Brightwater Joint Centre</div>
    <div class="contact">
      <p>48 Larkspur Ridge Road</p>
      <p>Suite 310, Elmhurst, OR 97045</p>
      <p class="row gap"><svg class="icon" width="7" height="7" viewBox="0 0 10 10"><path d="M2 0.5l2 2-1 1.5c.6 1.3 1.7 2.4 3 3l1.5-1 2 2-1.5 1.8C4.5 9.6.4 5.5.2 2z" fill="var(--sky)"/></svg>555 010 2468</p>
      <p class="row"><svg class="icon" width="8" height="6" viewBox="0 0 10 7"><rect width="10" height="7" fill="var(--sky)"/><path d="M0 0l5 4 5-4" stroke="#fff" fill="none"/></svg>info@brightwaterjoint.com</p>
      <p class="row"><svg class="icon" width="7" height="7" viewBox="0 0 10 10"><circle cx="5" cy="5" r="4.5" fill="none" stroke="var(--sky)"/><path d="M.5 5h9M5 .5c-2.5 3-2.5 6 0 9M5 .5c2.5 3 2.5 6 0 9" fill="none" stroke="var(--sky)" stroke-width=".8"/></svg>www.brightwaterjoint.com</p>
    </div>
    <div class="badge badge--college" role="img" aria-label="Crestmoor Lindell College of Surgeons badge"></div>
    <div class="badge badge--association" role="img" aria-label="Varenwood Bone Health Association badge"></div>
    <svg class="wave" viewBox="0 0 579 63" preserveAspectRatio="none" aria-hidden="true">
      <path d="M0 19 Q200 60 579 4 Q230 58 0 33 Z" fill="var(--sky)"/>
      <path d="M0 33 Q220 66 579 4 L579 63 L0 63 Z" fill="var(--navy)"/>
    </svg>
  </section>

  <section class="card card--front" aria-label="Business card">
    <div class="brand"><span class="brand__dot"></span>The Brightwater Joint Centre</div>
    <div class="badge badge--college" role="img" aria-label="Crestmoor Lindell College of Surgeons badge"></div>
    <div class="badge badge--association" role="img" aria-label="Varenwood Bone Health Association badge"></div>
    <div class="divider"></div>
    <div class="contact">
      <p class="person__name">Dana Whitcombe</p>
      <p class="person__title">President</p>
      <p>48 Larkspur Ridge Road</p>
      <p>Suite 310, Elmhurst, OR 97045</p>
      <p class="row gap"><svg class="icon" width="9" height="9" viewBox="0 0 10 10"><path d="M2 0.5l2 2-1 1.5c.6 1.3 1.7 2.4 3 3l1.5-1 2 2-1.5 1.8C4.5 9.6.4 5.5.2 2z" fill="var(--sky)"/></svg>555 010 2468</p>
      <p class="row"><svg class="icon" width="9" height="7" viewBox="0 0 10 7"><rect width="10" height="7" fill="var(--sky)"/><path d="M0 0l5 4 5-4" stroke="#fff" fill="none"/></svg>info@brightwaterjoint.com</p>
      <p class="row"><svg class="icon" width="9" height="9" viewBox="0 0 10 10"><circle cx="5" cy="5" r="4.5" fill="none" stroke="var(--sky)"/><path d="M.5 5h9M5 .5c-2.5 3-2.5 6 0 9M5 .5c2.5 3 2.5 6 0 9" fill="none" stroke="var(--sky)" stroke-width=".8"/></svg>www.brightwaterjoint.com</p>
    </div>
    <svg class="wave" viewBox="0 0 441 44" preserveAspectRatio="none" aria-hidden="true">
      <path d="M0 9 Q160 40 441 3 Q180 46 0 19 Z" fill="var(--sky)"/>
      <path d="M0 19 Q170 50 441 3 L441 44 L0 44 Z" fill="var(--navy)"/>
    </svg>
  </section>

  <section class="card card--appointment" aria-label="Appointment card">
    <div class="brand"><span class="brand__dot"></span>The Brightwater Joint Centre</div>
    <div class="appointment">
      <h2 class="appointment__title"><span>Next</span> Appointment</h2>
      <div class="field-row">Name:<span class="leader"></span></div>
      <div class="field-row">Time:<span class="leader leader--short"></span>
        <span class="option"><span class="check"></span>AM</span>
        <span class="option"><span class="check"></span>PM</span>
        Date:<span class="leader"></span></div>
      <div class="days">
        <span><span class="check"></span> MON</span>
        <span><span class="check"></span> TUES</span>
        <span><span class="check"></span> WED</span>
        <span><span class="check"></span>THUR</span>
        <span><span class="check"></span>FRI</span>
        <span><span class="check"></span> SAT</span>
      </div>
      <p class="note">If you are unable to keep your appointment, please call us as soon as possible</p>
    </div>
  </section>

</div>
</body>
</html>
```